Emerging automotive detailing business

I am starting a small automotive detailing business in hopes of becoming a well-known detailer to work on high end cars. I would like a card to reflect the high quality and time I put into my work. The name of the company is Bright Crest Detailing. I feel like it represents racecars getting off the line at the drag strip as well as an innuendo of "Up the Ladder". I do minor paint correction such as clay barring, multi-step buffing and polishing, waxing, hand washes, etc. I am always striving to learn more and improve my work. My goal is to have total customer satisfaction. This is a female run business but I do not want it to be very girly. Elegant is okay! I have pictures of my personal wrenfield attached, they do not need to be incorporated but if you can think of a cool way to use 1 or all of them, go for it!

Target Market(s)

Anyone that owns a vehicle. Preferably high end vehicles such as Valtori, Castellverde and Morvani but I will also happily work on any car, truck or suv no matter what brand.

Industry/Entity Type

Automotive

Contact Information for Business Card

Bright Crest Detailing
Mira Tolland
4175 Quenhollow Rd
Ashmere PA 17492
Cell phone- call/text- 717-555-0148
email- brightcrestdetails@maildrop-example.com
Instagram: @brightcrestdetailing
Facebook: facebook.com/brightcrestdetailing

Requirements
Must have
• Business name, my name, address, phone number. Listing that I do minor paint correction such as clay barring, multi-step buffing and polishing, waxing, hand washes, interior cleaning, and more. (This last part was in nice to haves but I have realized that I do really want it, so I moved it to must haves.) I want something that is different and eye-catching to my customers. Some people have done this very well with cards already submitted to me, but a lot have not. I didn't mess with the "look and feel bars" much because because I am pretty open to the overall design as long as it is not your basic run of the mill design.
Nice to have
• Something car related. Maybe an appointment time/date line. I do not have a logo, but if you would like to design one and incorporate it, that would be amazing!
Should not have
• Purple and Pink colors. Boring, basic, normal card.

```html
<!DOCTYPE html>
<html lang="en">
<head>
<meta charset="utf-8">
<title>Bright Crest Detailing – Business Card</title>
<link rel="stylesheet" href="https://fonts.googleapis.com/css2?family=Poiret+One&family=Questrial&display=swap">
<style>
  :root {
    --ink: #000000;
    --paper: #ffffff;
    --backdrop: #ececec;
    --card-shadow: rgba(0, 0, 0, 0.18);
  }
  * { margin: 0; padding: 0; box-sizing: border-box; }
  html, body {
    width: 1200px; height: 800px; overflow: hidden;
    background: var(--backdrop);
  }
  .canvas {
    position: relative; width: 1200px; height: 800px;
  }
  .card {
    position: absolute; top: 250px;
    width: 540px; height: 300px;
    overflow: hidden;
    box-shadow: 0 6px 18px var(--card-shadow);
  }
  .card--front { left: 40px; background: var(--paper); }
  .card--back { left: 620px; background: var(--ink); }
  .card__swoosh { position: absolute; inset: 0; width: 540px; height: 300px; }

  .brand-title {
    position: absolute; top: 24px; left: 0; width: 100%;
    text-align: center;
    font-family: "Poiret One", sans-serif;
    font-size: 42px; line-height: 52px;
    letter-spacing: 2px; text-transform: uppercase;
    color: var(--ink);
  }
  .owner {
    position: absolute; left: 26px; top: 198px;
    font-family: "Questrial", sans-serif;
    color: var(--paper);
  }
  .owner__name { font-size: 18px; letter-spacing: 0.5px; margin-bottom: 18px; }
  .owner__address { font-size: 14px; line-height: 19px; }

  .contact-list {
    position: absolute; right: 24px; top: 206px;
    list-style: none;
    font-family: "Questrial", sans-serif;
    font-size: 13px; line-height: 19.5px;
    color: var(--paper); text-align: right;
  }
  .contact-list li { display: flex; justify-content: flex-end; align-items: center; gap: 7px; }
  .contact-list svg { width: 14px; height: 14px; flex: none; }
  .social-square { width: 13px; height: 13px; background: var(--paper); border-radius: 2px; flex: none; }

  .services {
    position: absolute; top: 40px; left: 0; width: 100%;
    text-align: center;
    font-family: "Poiret One", sans-serif;
    font-size: 16.5px; line-height: 20px;
    letter-spacing: 0.6px; text-transform: uppercase;
    color: var(--paper);
  }
  .appointment {
    position: absolute; left: 34px; top: 210px; right: 30px;
    font-family: "Questrial", sans-serif;
    font-size: 13.5px; color: var(--ink);
  }
  .appointment__heading { display: flex; align-items: center; gap: 5px; }
  .appointment__heading svg { width: 16px; height: 16px; }
  .appointment__fields { display: flex; margin-top: 12px; padding-left: 20px; }
  .appointment__field { width: 196px; }
</style>
</head>
<body>
<main class="canvas">

  <section class="card card--front" aria-label="Business card front">
    <svg class="card__swoosh" viewBox="0 0 540 300" aria-hidden="true">
      <path d="M0 118 Q290 196 540 166 L540 300 L0 300 Z" fill="var(--ink)"/>
      <path d="M0 130 Q290 208 540 178" fill="none" stroke="var(--paper)" stroke-width="5"/>
    </svg>
    <h1 class="brand-title">Bright Crest<br>Detailing</h1>
    <div class="owner">
      <p class="owner__name">Mira Tolland</p>
      <p class="owner__address">4175 Quenhollow Rd<br>Ashmere, PA 17492</p>
    </div>
    <ul class="contact-list">
      <li>(717) 555-0148
        <svg viewBox="0 0 14 14" aria-hidden="true"><rect x="3.5" y="1" width="7" height="12" rx="1.3" fill="none" stroke="var(--paper)" stroke-width="1.4"/><rect x="6" y="10.3" width="2" height="1.2" fill="var(--paper)"/></svg>
      </li>
      <li>brightcrestdetails@maildrop-example.com
        <svg viewBox="0 0 14 14" aria-hidden="true"><rect x="1" y="3" width="12" height="8.5" fill="var(--paper)"/><path d="M1.5 3.5 L7 8 L12.5 3.5 M1.5 11 L5.5 7 M12.5 11 L8.5 7" fill="none" stroke="var(--ink)" stroke-width="1"/></svg>
      </li>
      <li>@brightcrestdetailing <span class="social-square"></span></li>
      <li>@brightcrestdetailing <span class="social-square"></span></li>
    </ul>
  </section>

  <section class="card card--back" aria-label="Business card back">
    <svg class="card__swoosh" viewBox="0 0 540 300" aria-hidden="true">
      <path d="M0 128 Q290 206 540 176 L540 300 L0 300 Z" fill="var(--paper)"/>
      <path d="M0 121 Q290 199 540 169" fill="none" stroke="var(--paper)" stroke-width="5"/>
    </svg>
    <p class="services">Minor paint correction;<br>Claying, multi-step buffing and polishing,<br>waxing, hand washes, interior cleaning and more!</p>
    <div class="appointment">
      <p class="appointment__heading">
        <svg viewBox="0 0 16 16" aria-hidden="true"><rect x="1.5" y="3" width="13" height="11.5" fill="none" stroke="var(--ink)" stroke-width="1.4"/><rect x="1.5" y="3" width="13" height="3" fill="var(--ink)"/><rect x="4" y="1" width="1.5" height="3" fill="var(--ink)"/><rect x="10.5" y="1" width="1.5" height="3" fill="var(--ink)"/><path d="M6 8.5 H10 L7.5 13" fill="none" stroke="var(--ink)" stroke-width="1.3"/></svg>
        Your next appointment:
      </p>
      <div class="appointment__fields">
        <span class="appointment__field">Time:</span>
        <span class="appointment__field">Date:</span>
      </div>
    </div>
  </section>

</main>
</body>
</html>
```